New Business Card Design Project LORVANTI-Italy

we are LORVANTI-Italy
our company in the market for 3 years we are luxury cosmetic company and its about time for a facelift :)
i will like to have elegant luxurious and unique business card
that will give the person that get it a unique, luxurious and elegant impression
I'm VERY OPEN FOR NEW IDEAS , even duo i add a few files of things that i see on line and i like them

i add my logo as well
my website is LORVANTI.COM
(if you would like to see the main style that we have)

Target Market(s)

adult that have money :)

Industry/Entity Type

Business

Contact Information for Business Card

Name - Dario Lorvanti
Position - CEO and CO Founder
address - 4817 E Halvern
telephone - 555-384-1926
email - dario@lorvanti.com
fax - 555-384-1926
website - LORVANTI.COM

Colors
000000
959595
fbee3e
ffffff

Requirements
Must have
• big logo in GOLD color
• elegant look
• impressive
Nice to have
• not must but maybe classy pattern background
• not must but maybe emblem
• maybe clear plastic business card
Should not have
• colors
• images

```html
<!DOCTYPE html>
<html lang="en">
<head>
<meta charset="utf-8">
<title>Lorvanti Italy – Business Card</title>
<link href="https://fonts.googleapis.com/css2?family=Tinos&family=Open+Sans:wght@400&display=swap" rel="stylesheet">
<style>
  :root {
    --stage: #c4c4c4;
    --card-black: #0d0d0d;
    --card-black-soft: #151515;
    --gold: #e2b93b;
    --gold-deep: #c99a22;
    --white: #ffffff;
    --pattern-grey: #2a2a2a;
  }
  * { margin: 0; padding: 0; box-sizing: border-box; }
  html, body { width: 1200px; height: 900px; overflow: hidden; }
  body {
    background: var(--stage);
    position: relative;
    font-family: "Open Sans", Arial, sans-serif;
  }
  .card {
    position: absolute;
    top: 184px;
    width: 302px;
    height: 490px;
    border-radius: 11px;
    overflow: hidden;
    text-align: center;
  }
  .card--front { left: 299px; background: linear-gradient(180deg, var(--card-black-soft), var(--card-black)); }
  .card--back  { left: 645px; background: var(--card-black); }

  .emblem-ring {
    position: absolute;
    border: 3px solid var(--gold);
    border-radius: 50%;
  }
  .card--front .emblem-ring { left: 98px; top: 46px; width: 104px; height: 104px; }

  .brand-name {
    position: absolute; left: 0; right: 0;
    font-family: "Tinos", "Times New Roman", serif;
    color: var(--gold);
    letter-spacing: 1px;
  }
  .card--front .brand-name { top: 168px; font-size: 44px; line-height: 52px; }
  .brand-rule {
    position: absolute; left: 35px; width: 231px; top: 225px;
    height: 2px; background: var(--gold);
  }
  .brand-country {
    position: absolute; left: 0; right: 0; top: 234px;
    font-family: "Tinos", "Times New Roman", serif;
    font-size: 18px; color: var(--gold); letter-spacing: 1px;
  }
  .person-name {
    position: absolute; left: 0; right: 0; top: 302px;
    font-family: "Tinos", "Times New Roman", serif;
    font-size: 19px; color: var(--gold); letter-spacing: .5px;
  }
  .person-role {
    position: absolute; left: 0; right: 0; top: 328px;
    font-size: 12.5px; color: var(--white);
  }
  .contact-icons {
    position: absolute; left: 0; right: 0; top: 357px;
    display: flex; justify-content: center; gap: 7px;
  }
  .contact-icons svg { width: 15px; height: 15px; }
  .contact-list {
    position: absolute; left: 0; right: 0; top: 378px;
    list-style: none; font-size: 12.5px; line-height: 18px; color: var(--white);
  }
  .contact-rule {
    position: absolute; left: 100px; width: 101px; top: 441px;
    height: 1px; background: var(--gold);
  }
  .address {
    position: absolute; left: 0; right: 0; top: 451px;
    font-size: 12.5px; color: var(--white);
  }

  .pattern-band {
    position: absolute; left: 0; right: 0;
  }
  .pattern-band--top { top: 0; height: 120px; background: linear-gradient(180deg, var(--pattern-grey), var(--card-black)); }
  .pattern-band--bottom { bottom: 0; height: 100px; background: linear-gradient(0deg, var(--pattern-grey), var(--card-black)); }

  .card--back .emblem-ring {
    left: 59px; top: 141px; width: 186px; height: 186px;
    display: flex; align-items: center; justify-content: center;
  }
  .card--back .brand-name { position: static; font-size: 28px; }
  .website {
    position: absolute; left: 0; right: 0; top: 391px;
    font-family: "Tinos", "Times New Roman", serif;
    font-size: 16px; color: var(--gold); letter-spacing: .5px;
  }
</style>
</head>
<body>

<section class="card card--front" aria-label="Card front">
  <div class="emblem-ring" aria-hidden="true"></div>
  <div class="brand-name">LORVANTI</div>
  <div class="brand-rule"></div>
  <div class="brand-country">ITALY</div>

  <div class="person-name">DARIO LORVANTI</div>
  <div class="person-role">CEO and CO Founder</div>

  <div class="contact-icons" aria-hidden="true">
    <svg viewBox="0 0 16 16"><circle cx="8" cy="8" r="8" fill="var(--gold)"/><path d="M4 6.5c0-1.2 8-1.2 8 0v1H10V6.8H6v.7H4z M5 8.5h6l1 3H4z" fill="var(--card-black)"/></svg>
    <svg viewBox="0 0 16 16"><circle cx="8" cy="8" r="8" fill="var(--gold)"/><rect x="5.5" y="3.5" width="5" height="3" fill="var(--card-black)"/><rect x="4" y="7" width="8" height="4" rx="1" fill="var(--card-black)"/><rect x="5.5" y="10" width="5" height="2.5" fill="var(--card-black)"/></svg>
    <svg viewBox="0 0 16 16"><circle cx="8" cy="8" r="8" fill="var(--gold)"/><rect x="4" y="5" width="8" height="6" fill="var(--card-black)"/><path d="M4 5l4 3.5L12 5" stroke="var(--gold)" stroke-width="1" fill="none"/></svg>
  </div>
  <ul class="contact-list">
    <li>555-384-1926</li>
    <li>555-384-1926</li>
    <li>dario@lorvanti.com</li>
  </ul>
  <div class="contact-rule"></div>
  <div class="address">4817 E Halvern</div>
</section>

<section class="card card--back" aria-label="Card back">
  <div class="pattern-band pattern-band--top" role="img" aria-label="Faint grey geometric pattern along the top edge"></div>
  <div class="pattern-band pattern-band--bottom" role="img" aria-label="Faint grey geometric pattern along the bottom edge"></div>
  <div class="emblem-ring">
    <span class="brand-name">LORVANTI</span>
  </div>
  <div class="website">LORVANTI.COM</div>
</section>

</body>
</html>
```